Company or website name
- dalewintham.com
- Links to the website
- Vita Forge
- Describe your company and organization and target audience
- Founded by celebrity personal trainer and media personality Dale Wintham, Vita Forge provides high quality on-site fitness and wellness classes, and personal trainers for businesses and residential gyms throughout New York City. Our target audience are residents of high end buildings in NYC, that expect excellence and luxury
- The design should have the following
- This is a 24"x36" Poster for a complimentary event at a high end building. I would like the poster to look high end, luxury and simple and chique. The words should be clear and easy to read. It would be great to have a final copy that we can send to the printer and one which we can edit for future events Here is the text: The Halcott Spires Gym Complimentary Fitness & Wellness Event Complimentary Yoga, Pilates & Interval Training Bootcamp Classes PLUS: 30 Minute Private Training Sessions *Kids Karate Classes Also Available Saturday May 18th, 25th & June 1st Time: 9:00am - 12:15pm Halcott Spires Gym Schedule: 9:00am - 9:30am Yoga 9:45am - 10:15am Interval Training Bootcamp 11:45am -12:15pm Pilates 9:00am - 12:00pm Private Training Sessions Special Introductory Rate on Future Packages During Promotion www.Vitaforge.tv Info@vitaforge.tv
- Other Facts

```html
<!DOCTYPE html>
<html lang="en">
<head>
<meta charset="utf-8">
<title>Vita Forge – Complimentary Fitness &amp; Wellness Event</title>
<link rel="stylesheet" href="https://fonts.googleapis.com/css2?family=Oswald:wght@500;700&family=Montserrat:wght@300;600;800&family=Arimo:ital,wght@0,400;0,700;1,700&display=swap">
<style>
  :root {
    --page: #ffffff;
    --ink: #07090c;
    --night: #0b1018;
    --royal: #1d3f86;
    --steel: #2c4a70;
    --sky: #3b6db0;
    --glow: #3b7a2c;
    --band: #1c3a1c;
    --white: #ffffff;
    --yellow: #f4e817;
    --skin: #9a7460;
  }
  * { margin: 0; padding: 0; box-sizing: border-box; }
  html, body { width: 1200px; height: 961px; overflow: hidden; background: var(--page); }
  .poster {
    position: absolute; left: 284px; top: 7px; width: 632px; height: 948px;
    background:
      radial-gradient(ellipse 70% 40% at 45% 42%, #2a56a8 0%, #183468 45%, transparent 80%),
      linear-gradient(180deg, var(--night) 0%, #101a2c 40%, var(--ink) 100%);
    overflow: hidden; color: var(--white);
    font-family: "Arimo", Arial, sans-serif;
  }
  .event-band {
    position: absolute; left: 0; top: 569px; width: 100%; height: 178px;
    background: linear-gradient(90deg, #13231a 0%, var(--band) 30%, #2e5a26 50%, var(--band) 70%, #13231a 100%);
  }
  .athlete-photo {
    position: absolute; left: 170px; top: 22px; width: 250px; height: 840px;
    border-radius: 120px 120px 60px 60px;
    background: radial-gradient(ellipse 50% 45% at 50% 35%, var(--skin) 0%, #5a4538 45%, rgba(30,30,30,0.0) 100%);
    box-shadow: 0 0 40px rgba(80,190,60,0.35);
  }
  .side-title {
    position: absolute; left: 32px; top: 555px; transform-origin: 0 0; transform: rotate(-90deg);
    white-space: nowrap; line-height: 1;
  }
  .side-title .name { font-family: "Montserrat", sans-serif; font-weight: 800; font-size: 54px; color: var(--steel); letter-spacing: 1px; }
  .side-byline {
    position: absolute; left: 118px; top: 555px; transform-origin: 0 0; transform: rotate(-90deg);
    white-space: nowrap; font-family: "Montserrat", sans-serif; font-weight: 300; font-size: 54px;
    color: var(--sky); line-height: 1;
  }
  .side-rule { position: absolute; left: 102px; top: 40px; width: 1px; height: 515px; background: var(--sky); }
  .brand-box {
    position: absolute; left: 419px; top: 3px; width: 192px; height: 277px; background: #000;
    display: flex; flex-direction: column; align-items: center; justify-content: center; gap: 14px;
  }
  .brand-box .mark { width: 16px; height: 16px; background: var(--white); }
  .brand-box .brand-name { font-family: "Montserrat", sans-serif; font-weight: 600; font-size: 24px; color: var(--white); letter-spacing: 1px; }
  .schedule {
    position: absolute; left: 425px; top: 326px; width: 180px; text-align: center;
    font-size: 12.5px; line-height: 21px; text-shadow: 0 1px 2px #000;
  }
  .schedule .tight { line-height: 17px; }
  .schedule .head { font-weight: 700; }
  .schedule .slot { font-weight: 700; font-style: italic; }
  .headline {
    position: absolute; left: 0; top: 586px; width: 100%; text-align: center;
    font-family: "Oswald", sans-serif; font-weight: 700; font-size: 39px; line-height: 38px;
    letter-spacing: 5px; text-transform: uppercase; text-shadow: 2px 2px 3px #000;
  }
  .headline-sub { position: absolute; left: 0; top: 715px; width: 100%; text-align: center; font-size: 17px; font-weight: 700; }
  .bonus { position: absolute; left: 10px; top: 786px; width: 220px; text-align: center; }
  .bonus .big { font-family: "Oswald", sans-serif; font-weight: 700; font-size: 38px; line-height: 38px; color: var(--yellow); }
  .bonus .list { margin-top: 10px; font-style: italic; font-weight: 700; font-size: 14.5px; line-height: 22px; }
  .promo { position: absolute; left: 250px; top: 796px; width: 380px; text-align: center; font-family: "Oswald", sans-serif; font-weight: 500; }
  .promo .lead { font-size: 18px; line-height: 24px; }
  .promo .rate { font-size: 27px; line-height: 34px; color: var(--yellow); font-weight: 700; }
  .promo .note { font-size: 18px; line-height: 26px; }
  .contact { position: absolute; left: 250px; top: 893px; width: 380px; text-align: center; font-size: 16px; font-weight: 700; word-spacing: 4px; }
</style>
</head>
<body>
  <main class="poster">
    <div class="event-band"></div>

    <div class="side-title"><span class="name">VITA FORGE</span></div>
    <div class="side-rule"></div>
    <div class="side-byline">BY DALE WINTHAM</div>

    <div class="athlete-photo" role="img" aria-label="Photo of a fit woman in black sportswear throwing a punch mid-stride, with a green glow around her"></div>

    <div class="brand-box">
      <span class="mark"></span>
      <span class="brand-name">VITA FORGE</span>
    </div>

    <section class="schedule">
      <p>Also Available Saturday</p>
      <p>May 18th, 25th &amp; June 1st</p>
      <p>9:00am - 12:15pm</p>
      <p class="head">Schedule:</p>
      <div class="tight">
        <p class="slot">Halcott Spires Gym</p>
        <p>9:00am - 9:30am</p>
        <p class="slot">Yoga</p>
        <p>9:45am - 10:15am</p>
        <p class="slot">Interval Training Bootcamp</p>
        <p>11:45am -12:15pm</p>
        <p class="slot">Pilates</p>
        <p>9:00am - 12:00pm</p>
      </div>
    </section>

    <h1 class="headline">The Halcott Spires Gym<br>Complimentary Fitness<br>&amp; Wellness Event</h1>
    <p class="headline-sub">Complimentary Yoga, Pilates &amp; Interval Training Bootcamp Classes</p>

    <section class="bonus">
      <p class="big">PLUS: 30<br>MINUTE</p>
      <p class="list">Private Training Sessions<br>*Kids Karate Classes</p>
    </section>

    <section class="promo">
      <p class="lead">PRIVATE TRAINING SESSIONS</p>
      <p class="rate">SPECIAL INTRODUCTORY RATE</p>
      <p class="note">ON FUTURE PACKAGES DURING PROMOTION</p>
    </section>

    <p class="contact">www.Vitaforge.tv Info@vitaforge.tv</p>
  </main>
</body>
</html>
```